BRIGHTHOLD PROPERTY MANAGEMENT INC. WEBSITE

Please make the website more family-friendly.

I want a website to help me build my property management business by adding listing properties and creating an online application. Im open to any other ideas.
I want a WordPress designer to code it.

Here is my current website. www.brighthold.biz

IDEA: I like the website design https://www.pelicanclimateservices.com/

Thank you

Tom

Number of Pages Required

5+ page

```html
<!DOCTYPE html>
<html lang="en">
<head>
<meta charset="UTF-8">
<title>Brighthold Property Management Inc.</title>
<link rel="stylesheet" href="https://fonts.googleapis.com/css2?family=Plus+Jakarta+Sans:wght@400;500;600;700;800&display=swap">
<style>
:root{
  --red:#d0111b;
  --red-dark:#7b0b0b;
  --ink:#161616;
  --body:#333;
  --white:#fff;
  --wood:#a0683c;
  --wood-dark:#5a3a22;
  --line:#e9e9ee;
}
*{box-sizing:border-box;margin:0;padding:0}
html,body{width:1200px;height:3973px;overflow:hidden}
body{font-family:"Plus Jakarta Sans",sans-serif;color:var(--ink);background:var(--white);position:relative}
.abs{position:absolute}
.photo{position:absolute}
.btn{position:absolute;display:flex;align-items:center;justify-content:center;font-size:17px;font-weight:500;text-decoration:none;height:46px}
.btn-solid{background:var(--red);color:var(--white)}
.btn-outline{border:2px solid var(--red);color:var(--red);background:var(--white)}
.btn-ghost{border:2px solid var(--white);color:var(--white)}
.rule{position:absolute;height:5px;background:var(--red)}
.h2{position:absolute;font-size:50px;font-weight:700;line-height:1.2;letter-spacing:-1px;text-transform:uppercase}
.copy{position:absolute;font-size:16.5px;line-height:29.5px;color:var(--body)}

/* hero */
.hero{position:absolute;left:0;top:0;width:1200px;height:733px;background:linear-gradient(180deg,#3e3430 0%,#6d4a31 45%,var(--wood) 100%)}
.hero-shade{position:absolute;inset:0;background:linear-gradient(90deg,rgba(0,0,0,.35),rgba(0,0,0,0) 70%)}
.nav{position:absolute;left:0;top:0;width:1200px;height:80px}
.brand{position:absolute;left:100px;top:32px;color:var(--white);font-weight:800;font-size:12px;letter-spacing:.3px;line-height:16px;white-space:nowrap}
.menu{position:absolute;left:198px;top:30px;display:flex;font-size:17px;color:var(--white);font-weight:500;white-space:nowrap}
.menu span{margin-right:21px;display:flex;align-items:center;gap:7px}
.menu span.dd::after{content:"";border-left:6px solid transparent;border-right:6px solid transparent;border-top:7px solid var(--white)}
.login{position:absolute;left:995px;top:21px;width:105px;height:38px;background:var(--red);color:var(--white);font-size:14px;font-weight:600;display:flex;align-items:center;justify-content:center}
.hero h1{position:absolute;left:100px;top:172px;width:1000px;font-size:68px;line-height:83px;font-weight:700;color:var(--white);letter-spacing:-1px;white-space:nowrap}
.hero p{position:absolute;left:100px;top:350px;width:760px;font-size:27px;line-height:46px;color:var(--white)}

/* services */
.eyebrow{position:absolute;left:0;width:1200px;text-align:center;top:1468px;font-size:26px;font-weight:500}
.services-title{left:0;width:1200px;text-align:center;top:1510px}
.svc-label{position:absolute;font-size:20.5px;font-weight:500;line-height:25px}
.svc-label.r{text-align:right}

/* cta */
.cta{position:absolute;left:0;top:3006px;width:1200px;height:534px;background:linear-gradient(180deg,#8fb0d4 0%,#c9b7a2 45%,#a89a88 80%,#6d6a63 100%)}
.cta-box{position:absolute;left:185px;top:102px;width:830px;height:330px;background:rgba(214,30,36,.82);color:var(--white);text-align:center}
.cta-box h2{position:absolute;left:0;top:45px;width:100%;font-size:48px;font-weight:700;letter-spacing:-1px}
.cta-box .bar{position:absolute;left:325px;top:124px;width:223px;height:5px;background:var(--white)}
.cta-box p{position:absolute;left:115px;top:162px;width:600px;font-size:20.5px;line-height:25px}

/* footer */
.footer{position:absolute;left:0;top:3540px;width:1200px;height:433px;background:var(--red-dark);color:var(--white)}
.foot-brand{position:absolute;left:95px;top:140px;width:230px;text-align:center;font-size:29px;font-weight:700;letter-spacing:1px}
.foot-brand small{display:block;font-size:10px;font-weight:500;letter-spacing:1.5px;margin-top:4px}
.socials{position:absolute;left:110px;top:236px;display:flex;gap:16px}
.socials span{width:24px;height:24px;border-radius:50%;background:var(--white);display:block}
.foot-col{position:absolute;font-size:16.5px;line-height:29px}
.foot-col h3{font-size:22px;line-height:28px;font-weight:700;margin-bottom:20px}
.contact-line{display:flex;align-items:center;gap:10px}
.subscribe{position:absolute;left:788px;top:77px;width:340px}
.subscribe h3{font-size:24px;font-weight:700;margin-bottom:10px}
.subscribe p{font-size:16.5px;line-height:29px}
.field{position:absolute;left:0;top:142px;width:250px;height:34px;background:var(--white);color:#999;font-size:12px;padding:9px 10px}
.field-btn{position:absolute;left:250px;top:142px;width:84px;height:34px;background:var(--red);font-size:14px;font-weight:600;display:flex;align-items:center;justify-content:center}
.foot-rule{position:absolute;left:67px;top:348px;width:1066px;height:2px;background:rgba(255,255,255,.8)}
.legal{position:absolute;left:67px;top:367px;font-size:10px}
</style>
</head>
<body>

<!-- Hero -->
<section class="hero">
  <div class="photo" role="img" aria-label="House model and keys on a wooden table" style="inset:0;background:radial-gradient(ellipse at 75% 55%,#c8894f 0%,rgba(160,104,60,0) 55%)"></div>
  <div class="hero-shade"></div>
  <nav class="nav">
    <div class="brand">BRIGHTHOLD</div>
    <div class="menu">
      <span class="dd">Listing</span><span class="dd">Owners</span><span class="dd">Prospect Tenants</span><span>Community</span><span class="dd">About</span><span class="dd">Mortage</span><span>Contact</span>
    </div>
    <div class="login">Login</div>
  </nav>
  <h1>BRIGHTHOLD PROPERTY<br>MANAGEMENT INC.</h1>
  <p>We are committed to helping you and making being a home provider hassle free</p>
  <a class="btn btn-solid" style="left:100px;top:458px;width:200px">Request Demo</a>
  <a class="btn btn-ghost" style="left:313px;top:458px;width:200px">Learn More</a>
</section>

<!-- Helping -->
<div class="photo" role="img" aria-label="Family sitting under a sketched house drawing" style="left:100px;top:833px;width:492px;height:533px;background:linear-gradient(160deg,#f1f1f1 0%,#d9d9d9 60%,#bfc3c6 100%)"></div>
<h2 class="h2" style="left:640px;top:880px;width:480px">We are commited to helping you</h2>
<div class="rule" style="left:640px;top:1013px;width:265px"></div>
<p class="copy" style="left:640px;top:1048px;width:460px">We truly feel excited and gratified when helping individuals meet their real estate needs. We pride ourselves on being honest, trustworthy, and knowledgeable in the real estate market. We know how important it is to find your dream home or receive the best offer for your property. Therefore we will make it our responsibility to help you achieve those goals.</p>
<a class="btn btn-solid" style="left:640px;top:1277px;width:182px">CONTACT US</a>
<a class="btn btn-outline" style="left:840px;top:1277px;width:182px">LEARN MORE</a>

<!-- Services -->
<div class="eyebrow">BRIGHTHOLD</div>
<h2 class="h2 services-title">Property Management Services</h2>
<div class="rule" style="left:467px;top:1585px;width:266px"></div>

<svg class="abs" style="left:0;top:1600px" width="1200" height="700" viewBox="0 1600 1200 700" aria-hidden="true">
  <circle cx="600" cy="1905" r="230" fill="none" stroke="var(--line)" stroke-width="4"/>
  <defs><radialGradient id="hub" cx="50%" cy="40%" r="60%"><stop offset="0" stop-color="#7fae4a"/><stop offset=".7" stop-color="#4d7f2e"/><stop offset="1" stop-color="#8b8a92"/></radialGradient></defs>
  <circle cx="600" cy="1905" r="182" fill="url(#hub)"/>
  <g fill="var(--red)">
    <circle cx="435" cy="1727" r="6"/><circle cx="762" cy="1727" r="6"/>
    <circle cx="369" cy="1882" r="6"/><circle cx="831" cy="1882" r="6"/>
    <circle cx="447" cy="2065" r="6"/><circle cx="750" cy="2065" r="6"/>
    <circle cx="600" cy="2122" r="6"/>
  </g>
  <g>
    <g transform="translate(378 1707)"><circle r="37" fill="var(--red)" stroke="#f6c9cb" stroke-width="4"/><rect x="-12" y="-15" width="24" height="30" rx="2" fill="none" stroke="#fff" stroke-width="2.5"/><path d="M-7 -8h14M-7 0h4M1 0h6M-7 7h4M1 7h6" stroke="#fff" stroke-width="2.5"/></g>
    <g transform="translate(819 1707)"><circle r="37" fill="var(--red)" stroke="#f6c9cb" stroke-width="4"/><path d="M-14 14v-14l14-13 14 13v14zM-4 14v-10h8v10" fill="none" stroke="#fff" stroke-width="2.5"/></g>
    <g transform="translate(312 1882)"><circle r="37" fill="var(--red)" stroke="#f6c9cb" stroke-width="4"/><path d="M-10-15h14l7 7v23h-21z M-5-6h8M-5 1h12M-5 8h10" fill="none" stroke="#fff" stroke-width="2.5"/></g>
    <g transform="translate(888 1882)"><circle r="37" fill="var(--red)" stroke="#f6c9cb" stroke-width="4"/><rect x="-15" y="-12" width="30" height="24" rx="3" fill="none" stroke="#fff" stroke-width="2.5"/><circle r="6" fill="none" stroke="#fff" stroke-width="2.5"/></g>
    <g transform="translate(378 2067)"><circle r="37" fill="var(--red)" stroke="#f6c9cb" stroke-width="4"/><circle cy="-5" r="8" fill="none" stroke="#fff" stroke-width="2.5"/><path d="M-15 12q7-6 15 0t15 0" fill="none" stroke="#fff" stroke-width="2.5"/></g>
    <g transform="translate(817 2067)"><circle r="37" fill="var(--red)" stroke="#f6c9cb" stroke-width="4"/><rect x="-14" y="-14" width="22" height="26" fill="none" stroke="#fff" stroke-width="2.5"/><circle cx="4" cy="3" r="6" fill="none" stroke="#fff" stroke-width="2.5"/><path d="M8 8l7 7" stroke="#fff" stroke-width="2.5"/></g>
    <g transform="translate(600 2176)"><circle r="37" fill="var(--red)" stroke="#f6c9cb" stroke-width="4"/><path d="M-13-13l26 26M13-13l-26 26" stroke="#fff" stroke-width="3" stroke-linecap="round"/></g>
  </g>
</svg>
<div class="abs" role="img" aria-label="House with a for rent sign" style="left:418px;top:1723px;width:364px;height:364px;border-radius:50%"></div>
<div class="abs" style="left:418px;top:1930px;width:364px;text-align:center;color:#fff;font-size:32px;font-weight:700;letter-spacing:1px">BRIGHTHOLD</div>

<div class="svc-label r" style="left:188px;top:1683px;width:140px">Accounting<br>Services</div>
<div class="svc-label" style="left:869px;top:1695px">Leasing</div>
<div class="svc-label r" style="left:100px;top:1855px;width:162px">Mortage<br>Utility Payment</div>
<div class="svc-label" style="left:938px;top:1851px">Security<br>Deposits</div>
<div class="svc-label r" style="left:188px;top:2043px;width:135px">Rent<br>Collection</div>
<div class="svc-label" style="left:869px;top:2046px">Inspections<br>of Property</div>
<div class="svc-label" style="left:450px;top:2224px;width:300px;text-align:center">Repair &amp; Maintenance<br>Service</div>

<!-- Commitment -->
<h2 class="h2" style="left:100px;top:2424px;width:460px">Our Commitment</h2>
<div class="rule" style="left:100px;top:2500px;width:266px"></div>
<p class="copy" style="left:100px;top:2534px;width:465px">Having the right property manager means having an agent who is committed to helping you and making being a home provider hassle free. I believe clear communication, work ethic, time management, staying focused and knowledgeable goes a long way in my business.</p>
<p class="copy" style="left:100px;top:2696px;width:465px">This commitment level has helped us build a remarkable track record of delivering results and maintaining a long lasting business partnership with our clients.</p>
<a class="btn btn-solid" style="left:100px;top:2810px;width:183px">CONTACT US</a>
<a class="btn btn-outline" style="left:300px;top:2810px;width:183px">LEARN MORE</a>
<div class="photo" role="img" aria-label="Rental contract on a clipboard with keys and a pen" style="left:607px;top:2373px;width:493px;height:533px;background:linear-gradient(160deg,#d5d8de 0%,#eef0f3 50%,#c7cad0 100%)"></div>

<!-- CTA -->
<section class="cta" role="img" aria-label="Suburban houses under a blue sky">
  <div class="cta-box">
    <h2>WHAT ARE YOU WAITING FOR?</h2>
    <div class="bar"></div>
    <p>Call Today &amp; Get 1 Month Property Management Fee Off. $120 Value!!</p>
    <a class="btn btn-ghost" style="left:155px;top:228px;width:252px">CONTACT US</a>
    <a class="btn btn-ghost" style="left:423px;top:228px;width:252px">LEARN MORE</a>
  </div>
</section>

<!-- Footer -->
<footer class="footer">
  <div class="foot-brand">BRIGHTHOLD<small>PROPERTY MANAGEMENT &amp; SERVICES</small></div>
  <div class="socials" aria-label="Social links"><span></span><span></span><span></span><span></span><span></span></div>
  <div class="foot-col" style="left:436px;top:68px;width:300px">
    <h3>BRIGHTHOLD PROPERTY MANAGEMENT INC.</h3>
    <div>4870 Maple Crest Ave. #112<br>Riverton , CA 95690</div>
    <div style="margin-top:10px">Contact Us</div>
    <div class="contact-line"><svg width="14" height="14" viewBox="0 0 24 24"><path fill="#fff" d="M6.6 10.8a15.1 15.1 0 0 0 6.6 6.6l2.2-2.2c.3-.3.7-.4 1-.2 1.1.4 2.3.6 3.6.6.6 0 1 .4 1 1V20c0 .6-.4 1-1 1A17 17 0 0 1 3 4c0-.6.4-1 1-1h3.5c.6 0 1 .4 1 1 0 1.2.2 2.4.6 3.6.1.3 0 .7-.2 1z"/></svg>(555) 014-2870</div>
    <div class="contact-line"><svg width="14" height="14" viewBox="0 0 24 24"><rect x="6" y="2" width="12" height="20" rx="2" fill="none" stroke="#fff" stroke-width="2.5"/></svg>(555) 014-2870</div>
  </div>
  <div class="subscribe">
    <h3>SUBSCRIBE</h3>
    <p>Enter your email address to register to our newsletter subscription</p>
    <div class="field">Enter e-mail address</div>
    <div class="field-btn">Subscribe</div>
  </div>
  <div class="foot-rule"></div>
  <div class="legal">© 2024 Brighthold Management INC.. All rights reserved.</div>
</footer>

</body>
</html>
```